Heron Haulage needs Bussiness cards!

Our new trucking company needs business cards!
We need the same design with two different names and emails, everything else it's the same.
I have included our original logo so we can use it for the design.
Note: the logo to be used is the o e with the buffalo on the right side, next to the letters H and H.

Target Market(s)

Trucking, refrigerated transportation, freight

Industry/Entity Type

Business

Contact Information for Business Card

Card #1:
Marcus Whitfield
marcuswhitfield@heronhaulage.example
1-855-317-6094
(737)238-7160
4117 W. Larkin Ave.
Cedar Bend, OK 78590
www.heronhaulage.example

Card#2:
Rosalba Quintero
rosalba@heronhaulage.example
1-855-317-6094
(737)238-7160
4117 W. Larkin Ave.
Cedar Bend, OK 78590
www.heronhaulage.example

Font styles to use
Sans Serif

Colors
0655a3
ec1f27
ffffff

Requirements
Must have
• our logo
Nice to have
• roads on background,

```html
<!DOCTYPE html>
<html lang="en">
<head>
<meta charset="utf-8">
<title>Heron Haulage – Business Card</title>
<link rel="stylesheet" href="https://fonts.googleapis.com/css2?family=Roboto+Condensed:wght@400;700&display=swap">
<style>
  :root {
    --navy: #1b3a6b;
    --blue: #0655a3;
    --red: #ec1f27;
    --white: #ffffff;
    --backdrop: #e9eaec;
    --card-shadow: rgba(0, 0, 0, 0.18);
  }
  * { box-sizing: border-box; margin: 0; padding: 0; }
  html, body {
    width: 1200px;
    height: 950px;
    overflow: hidden;
    background: var(--backdrop);
    font-family: "Roboto Condensed", Arial, sans-serif;
  }
  .canvas {
    width: 1200px;
    height: 950px;
    display: flex;
    flex-direction: column;
    align-items: center;
    justify-content: center;
    gap: 40px;
  }
  .card {
    position: relative;
    width: 760px;
    height: 434px;
    box-shadow: 0 10px 30px var(--card-shadow);
    overflow: hidden;
  }
  .card--front { background: var(--white); }
  .card--back { background: var(--navy); color: var(--white); }

  .wordmark {
    position: absolute;
    display: flex;
    align-items: center;
    gap: 18px;
    font-weight: 700;
    text-transform: uppercase;
    letter-spacing: 1px;
    line-height: 1;
    white-space: nowrap;
  }
  .wordmark__dot {
    width: 58px;
    height: 58px;
    border-radius: 50%;
    background: var(--red);
    flex: none;
  }
  .wordmark__name { font-size: 56px; }
  .card--front .wordmark { left: 50%; top: 50%; transform: translate(-50%, -50%); }
  .card--front .wordmark__name { color: var(--blue); }
  .card--back .wordmark { left: 200px; top: 150px; }
  .card--back .wordmark__name { color: var(--white); }

  .holder-name {
    position: absolute;
    right: 48px;
    top: 42px;
    font-size: 24px;
    font-weight: 700;
    text-transform: uppercase;
    letter-spacing: 0.5px;
  }
  .rule {
    position: absolute;
    height: 2px;
    background: var(--white);
  }
  .rule--upper-a { left: 420px; right: 40px; top: 238px; }
  .rule--upper-b { left: 40px; right: 40px; top: 262px; }
  .rule--lower { left: 40px; right: 40px; top: 384px; }
  .contact {
    position: absolute;
    left: 48px;
    right: 40px;
    top: 300px;
    font-size: 18px;
    font-weight: 400;
    font-style: normal;
    line-height: 1.55;
    white-space: nowrap;
  }
</style>
</head>
<body>
<main class="canvas">
  <section class="card card--front" aria-label="Card front">
    <div class="wordmark">
      <span class="wordmark__dot"></span>
      <span class="wordmark__name">Heron Haulage</span>
    </div>
  </section>

  <section class="card card--back" aria-label="Card back">
    <p class="holder-name">Marcus Whitfield</p>
    <div class="wordmark">
      <span class="wordmark__dot"></span>
      <span class="wordmark__name">Heron Haulage</span>
    </div>
    <div class="rule rule--upper-a"></div>
    <div class="rule rule--upper-b"></div>
    <address class="contact">
      <p>4117 W. Larkin Ave. Cedar Bend, OK 78590 &nbsp;P : 1-855-317-6094 &nbsp;M : (737)238-7160</p>
      <p>Email : marcuswhitfield@heronhaulage.example &nbsp;Web : www.heronhaulage.example</p>
    </address>
    <div class="rule rule--lower"></div>
  </section>
</main>
</body>
</html>
```